Website visual upgrade

I am seeking expressions of interest for the updating the visuals of my website www.kelvastaffing.net
I am basically seeking a simple,bold and visually strong graphic makeover.using existing or shortly to be modified text.

```html
<!DOCTYPE html>
<html lang="en">
<head>
<meta charset="utf-8">
<title>Kelva Staffing</title>
<link rel="stylesheet" href="https://fonts.googleapis.com/css2?family=Lato:wght@400;700&family=Arimo:wght@400;700&display=swap">
<style>
:root{
  --red:#c8102e;
  --ink:#1d1d1d;
  --grey-line:#c9c9c9;
  --panel:#efefef;
  --btn:#d6d6d6;
  --blue:#1a8fe0;
}
*{box-sizing:border-box;margin:0;padding:0}
html,body{width:1200px;height:747px;overflow:hidden;background:#fff;color:var(--ink)}
body{position:relative;font-family:'Arimo',Arial,sans-serif}
.heading{font-family:'Lato',Arial,sans-serif}
.abs{position:absolute}

.topbar{left:0;top:0;width:1200px;height:26px;border-bottom:1px solid var(--grey-line)}
.tab{top:0;height:26px;border:1px solid var(--grey-line);border-top:0;background:#f0f0f0;font:700 11.5px 'Lato',sans-serif;color:#444;display:flex;align-items:center;justify-content:center}
.field{top:4px;height:16px;border:1px solid #b9b9b9;background:#fff;font-size:7px;padding-left:5px;display:flex;align-items:center;justify-content:space-between;border-radius:2px}
.field .hint{background:#777;color:#fff;font-size:6.5px;padding:1px 5px;margin-right:2px;border-radius:2px}
.login-btn{top:4px;height:16px;border-radius:3px;font:400 9.5px 'Lato',sans-serif;display:flex;align-items:center;justify-content:center}
.login-btn.log{background:var(--btn);border:1px solid #aaa;color:#333}
.login-btn.sign{background:var(--blue);color:#fff}

.band{left:0;top:52px;width:1200px;height:50px;background:var(--red)}
.brand{left:250px;top:52px;width:254px;height:50px;background:#fff;display:flex;align-items:center;gap:8px;padding-left:12px}
.brand-dot{width:14px;height:14px;border-radius:50%;background:var(--ink)}
.brand-name{font:700 23px 'Lato',sans-serif;color:var(--red)}
.nav{left:513px;top:67px;display:flex;align-items:center;font:700 12px 'Lato',sans-serif;color:#fff}
.nav a{color:#fff;text-decoration:none;padding:2px 3px}
.nav a.current{background:#111}
.nav .sep{margin:0 5px;font-size:8px}

.headline{left:0;width:1200px;top:130px;text-align:center;font-weight:700;font-size:27px}
.subline{left:0;width:1200px;top:160px;text-align:center;font-weight:700;font-size:21px;color:var(--red)}

.card{top:235px;width:154px;height:196px}
.card .bar{position:absolute;left:0;top:0;width:6px;height:196px;background:var(--red)}
.card h2{position:absolute;left:15px;top:3px;font:400 17.5px 'Lato',sans-serif}
.card .box{position:absolute;left:6px;top:29px;width:148px;height:167px;border:1px solid #dcdcdc;border-left:0;padding:5px 8px}
.card h3{font:700 10.5px/1.25 'Lato',sans-serif;margin-bottom:14px}
.card p{font-size:8.3px;line-height:1.25;color:#333}
.more{display:inline-block;margin-top:10px;background:var(--btn);border:1px solid #bbb;font:700 8.5px 'Arimo',sans-serif;padding:3px 12px}
.countries{list-style:none;font-size:8.3px;color:#222}
.countries li{margin-bottom:6.3px}
.countries li::before{content:"•";color:var(--red);margin-right:2px}

.testimonials{left:250px;top:450px;width:700px;height:140px;background:var(--panel);text-align:center;padding:15px 12px 0}
.testimonials h2{font:700 27px 'Lato',sans-serif;margin-bottom:8px}
.testimonials p{font-size:8.6px;line-height:15.2px;color:#333}

.footnav{left:0;top:612px;width:1200px;height:27px;border-top:1px solid var(--grey-line);border-bottom:1px solid var(--grey-line)}
.footlinks{left:250px;top:618px;display:flex;gap:26px;font:700 12px 'Lato',sans-serif;color:#444}
.search{left:826px;top:617px;width:124px;height:15px;border:1px solid #bbb;font-size:7px;padding-left:5px;display:flex;align-items:center;justify-content:space-between;border-radius:2px}
.search .btn{width:14px;height:13px;background:#666;display:flex;align-items:center;justify-content:center}

.sitemap{left:250px;top:655px;font-size:8.6px;display:flex;gap:5px}
.copy{left:250px;top:675px;font-size:8.6px}
.support-title{left:797px;top:646px;font:400 18px 'Lato',sans-serif}
.badge{top:679px;height:38px}
</style>
</head>
<body>
<header>
  <div class="abs topbar"></div>
  <div class="abs tab" style="left:250px;width:67px">CLIENT</div>
  <div class="abs tab" style="left:316px;width:90px">JOB SEEKER</div>
  <div class="abs field" style="left:576px;width:124px">Email<span class="hint">?</span></div>
  <div class="abs field" style="left:708px;width:122px">Password<span class="hint">forgot?</span></div>
  <div class="abs login-btn log" style="left:839px;width:52px">Log in</div>
  <div class="abs login-btn sign" style="left:898px;width:52px">Sign up</div>

  <div class="abs band"></div>
  <div class="abs brand"><span class="brand-dot"></span><span class="brand-name">Kelva Staffing</span></div>
  <nav class="abs nav">
    <a class="current">Home</a><span class="sep">•</span>
    <a>Migration assistance</a><span class="sep">•</span>
    <a>Job seeker</a><span class="sep">•</span>
    <a>Useful links</a><span class="sep">•</span>
    <a>Support</a><span class="sep">•</span>
    <a>Contact us</a>
  </nav>
</header>

<main>
  <h1 class="abs headline heading">We are Executive search and selection specialists</h1>
  <div class="abs subline heading">We work exclusively with our clients</div>

  <section class="abs card" style="left:250px">
    <div class="bar"></div><h2>Who we are</h2>
    <div class="box"><h3>We have recruited for over 400 leading companies</h3>
      <p>Lorem Ipsum is simply dummy text of the printing and typesetting industry. Lorem Ipsum has been the industry's standard dummy text ever since the 1500s, when an unknown printer took a galley of type and scrambled it to make a type specimen book.</p>
      <span class="more">Read More</span></div>
  </section>
  <section class="abs card" style="left:431px">
    <div class="bar"></div><h2>What we do</h2>
    <div class="box"><h3>We are a specialist recruiter to the Health sector.</h3>
      <p>Lorem Ipsum is simply dummy text of the printing and typesetting industry. Lorem Ipsum has been the industry's standard dummy text ever since the 1500s, when an unknown printer took a galley of type and scrambled it to make a type specimen book.</p>
      <span class="more">Read More</span></div>
  </section>
  <section class="abs card" style="left:613px">
    <div class="bar"></div><h2>Our Approach</h2>
    <div class="box"><h3>Make your business<br>the best it can be</h3>
      <p>Lorem Ipsum is simply dummy text of the printing and typesetting industry. Lorem Ipsum has been the industry's standard dummy text ever since the 1500s, when an unknown printer took a galley of type and scrambled it to make a type specimen book.</p>
      <span class="more">Read More</span></div>
  </section>
  <section class="abs card" style="left:796px">
    <div class="bar"></div><h2 style="left:13px">Job Seeker's from</h2>
    <div class="box"><ul class="countries">
      <li>United Kingdom</li><li>Middle East</li><li>Zimbabwe</li><li>Malaysia</li><li>Singapore</li>
      <li>China</li><li>Philippines</li><li>New Zealand</li><li>Sounth Africa</li><li>Botswana</li>
    </ul></div>
  </section>

  <section class="abs testimonials">
    <h2>Client’s Testimonials</h2>
    <p>Lorem Ipsum is simply dummy text of the printing and typesetting industry. Lorem Ipsum has been the industry's standard dummy text ever since the 1500s, when an unknown printer took a galley of type and scrambled it to make a type specimen book. It has survived not only five centuries, but also the leap into electronic typesetting, remaining essentially unchanged. It was popularised in the 1960s with the release of Tessera sheets containing Lorem Ipsum passages, and more recently with desktop publishing software like Folio Layout including versions of Lorem Ipsum.</p>
  </section>
</main>

<footer>
  <div class="abs footnav"></div>
  <div class="abs footlinks"><span>Help</span><span>Contact</span><span>Fees</span><span>About</span><span>Blog</span><span>Jobs</span><span>Sitemap</span><span>Feedback</span></div>
  <div class="abs search">Search<span class="btn"><svg width="9" height="9" viewBox="0 0 10 10"><circle cx="4" cy="4" r="3" fill="none" stroke="#fff" stroke-width="1.4"/><line x1="6.2" y1="6.2" x2="9.2" y2="9.2" stroke="#fff" stroke-width="1.6"/></svg></span></div>

  <div class="abs sitemap"><span>Home</span>•<span>Who we are</span>•<span>Our Approach</span>•<span>What we do</span>•<span>Migration assistance</span>•<span>Job seeker</span>•<span>Useful links</span>•<span>Support</span>•<span>Contact us</span></div>
  <div class="abs copy">© Kelva Partners 2013</div>

  <div class="abs support-title">We Proudly Support</div>
  <div class="abs badge" role="img" aria-label="Supported charity badge" style="left:797px;width:54px;background:#111"></div>
  <div class="abs badge" role="img" aria-label="Supported fundraising badge" style="left:864px;width:86px;background:linear-gradient(90deg,#f6e7c8,#d9eef6)"></div>
</footer>
</body>
</html>
```